Nimbo31.com.au Website and company image design

We are looking for an exceptional website designer / company to work with our new Australian Hosting Company

Nimbo31 is a new Cloud Hosting company launching in Australia that provides Scalable, On Demand computing resources to the Australian Market Place. Scalable, On Demand ocmputing is a nice way of saying fully scalable / redundant Virtual Private Server.

We require a full company image to be developed along with a Logo and Website. There is scope for ongoing development (preferred) for the successful candidate.

Website developement will require extensive jQuery ability (sliders for ordering etc (see: http://www.hostrivo.com.au/virtual-dedicated-servers/253/kelp_vps.html).

Please communicate directly with me to establish full website scope and request further documentation / content.

Target Market(s)

Website Designers, programmers, technicians and large companies

Industry/Entity Type

It Company

Requirements
Must have
• Slider ordering system such as http://www.hostrivo.com.au/virtual-dedicated-servers/253/kelp_vps.html

Nice to have
• CMS backend system
Should not have
• Should NOT be a monster template copy!!!

```html
<!DOCTYPE html>
<html lang="en">
<head>
<meta charset="utf-8">
<title>Nimbo31 – Enterprise Hosting</title>
<link rel="stylesheet" href="https://fonts.googleapis.com/css2?family=Source+Sans+3:wght@400;600&display=swap">
<style>
:root{
  --ink:#3c3c3c;
  --muted:#7a7a7a;
  --brand:#3a8fd0;
  --navy:#1f4a72;
  --link:#2d8ad6;
  --accent:#a33a36;
  --line:#d6d6d6;
  --panel:#f1f8fc;
  --sky:#d9edf8;
  --footer:#ececec;
}
*{box-sizing:border-box;margin:0;padding:0}
html,body{width:1200px;height:2744px;overflow:hidden;background:#fff}
body{font-family:"Source Sans 3",sans-serif;color:var(--ink)}
.page{position:relative;width:1200px;height:2744px}
.abs{position:absolute}
.topbar{left:0;top:0;width:1200px;height:6px;background:var(--navy)}
/* header */
.logo-mark{left:18px;top:38px;width:62px;height:62px;border-radius:50%;background:var(--sky);border:2px solid var(--brand)}
.logo-name{left:115px;top:48px;font-size:41px;color:var(--brand);line-height:1}
.logo-tag{left:126px;top:110px;font-size:16px;color:var(--ink)}
.topnav{left:470px;top:14px;display:flex}
.topnav div{width:194px;height:74px;text-align:center;font-size:14px;line-height:28px;padding-top:16px;border-left:1px solid var(--line)}
.topnav div:first-child{border-left:0}
.topnav b{display:block;font-weight:400;text-transform:uppercase;letter-spacing:.3px}
.buttons{left:582px;top:113px;display:flex;gap:10px}
.buttons span{display:block;height:37px;line-height:35px;text-align:center;font-size:16px;border:1px solid #9cc5e3;border-radius:4px;background:linear-gradient(#f4fafe,#cfe6f6)}
/* hero */
.hero{left:49px;top:190px;width:1104px;height:377px;border:1px solid var(--line);background:linear-gradient(90deg,#fff 0,#f5f7f9 60%,#e9eef2 100%);box-shadow:0 14px 12px -10px rgba(0,0,0,.35)}
.hero-art{left:110px;top:25px;width:330px;height:300px;border-radius:8px;background:radial-gradient(circle at 45% 55%,#e0473d 0,#f2c032 30%,#7dbb3a 45%,#cfd3d6 70%,rgba(255,255,255,0) 78%)}
.hero-copy{left:585px;top:100px;color:#555}
.hero-copy h2{font-weight:400;font-size:29px;margin-bottom:14px}
.hero-copy p{font-size:21px;margin-left:50px;line-height:46px}
.dots{left:995px;top:327px;display:flex;gap:8px}
.dots i{width:17px;height:17px;border-radius:50%;background:#111}
.dots i:first-child{background:#6fc0ee}
/* plans */
.plan{top:644px;width:362px;height:408px;background:linear-gradient(#fff,#eeeeee);border:1px solid #eee;padding:28px 26px}
.plan h3{display:flex;align-items:center;gap:12px;font-weight:400;font-size:19px;text-transform:uppercase;height:40px;margin-bottom:18px}
.plan ul{list-style:none;font-size:14px;line-height:24px}
.plan li::before{content:"›";margin-right:10px;color:#666}
.price{display:flex;align-items:baseline;margin:14px 0 16px;font-size:14px}
.price strong{font-weight:400;font-size:27px;margin-left:20px}
.price a{margin-left:auto;color:var(--accent);text-decoration:none;font-size:16px}
.price.stacked{display:block;position:relative}
.price.stacked strong{display:block;margin:10px 0 0 22px}
.price.stacked a{position:absolute;right:0;top:38px}
/* hybrid + offers */
.hybrid{left:24px;top:1072px;width:759px;height:194px;background:linear-gradient(#e3f2fb,#cde6f5);border:1px solid #c3ddef;padding:56px 0 0 196px;font-size:21px;line-height:34px}
.hybrid .cost{font-size:26px}
.offers{left:814px;top:1072px;width:359px;height:194px;background:linear-gradient(#e3f2fb,#cde6f5);border:1px solid #c3ddef}
.offers h4{position:absolute;left:32px;top:16px;font-weight:400;font-size:20px}
.offer-photo{left:15px;top:52px;width:192px;height:130px;background:linear-gradient(135deg,#eaf3f9,#9fc3dc 55%,#5d7e98)}
.offer-text{left:220px;top:56px;width:128px;font-size:13px;line-height:21px;text-align:justify;color:#555}
.offer-link{right:20px;top:166px;font-size:14px;color:var(--accent)}
/* difference */
.difference{left:22px;top:1294px;width:1151px;height:540px;border:1px solid var(--line);box-shadow:0 0 8px rgba(0,0,0,.08)}
.difference h3{position:absolute;left:38px;top:30px;font-weight:400;font-size:21px}
.difference .intro{position:absolute;left:38px;top:70px;width:1060px;font-size:14px;line-height:24px;color:var(--muted)}
.tabs{left:35px;top:141px;width:1080px;height:47px;display:flex;border:1px solid var(--line);background:linear-gradient(#fff,#f3f3f3)}
.tabs span{line-height:45px;text-align:center;font-size:15px;color:#666;border-right:1px solid var(--line)}
.tabs .on{background:var(--navy);color:#fff}
.tab-panel{left:35px;top:188px;width:1080px;height:340px;background:var(--panel);border:1px solid var(--line);border-top:0}
.feat{width:300px}
.feat h5{font-weight:400;font-size:16px;color:var(--ink)}
.feat p{font-size:14px;line-height:24px;color:var(--muted)}
/* testimonials */
.section-title{font-weight:400;font-size:21px}
.client{top:1940px;width:245px;height:79px;display:flex;align-items:center;justify-content:center;font-size:30px;font-weight:600}
.client.a{border:1px solid #999;background:#fff;color:#2a6fb5}
.client.b{background:#8dbb3a;color:#fff}
.client.c{background:#1d3f77;color:#fff}
.quote{top:2031px;width:245px;height:129px;border:1px solid #ccc;border-radius:6px;background:linear-gradient(#fff,#f2f2f2);padding:20px 14px;font-size:13.5px;line-height:24px}
.quote::before{content:"";position:absolute;left:64px;top:-11px;width:18px;height:18px;background:#fff;border-left:1px solid #ccc;border-top:1px solid #ccc;transform:rotate(45deg)}
.quote b{display:block;font-weight:400;margin-bottom:8px}
/* feed */
.feed-icon{left:70px;top:2236px;width:46px;height:46px;border-radius:50%;background:#4ca8dc}
.feed-title{left:178px;top:2243px;font-size:21px;color:var(--link)}
.tweet{top:2318px;width:300px;font-size:13.5px;line-height:20px}
.tweet time{display:block;color:var(--link);margin-bottom:20px}
.tweet a{display:block;text-align:right;color:var(--link);text-decoration:none;margin-top:10px}
/* footer */
.footer{left:0;top:2474px;width:1200px;height:270px;background:var(--footer);border-top:1px solid #ddd}
.fcol{font-size:14.5px;line-height:27px}
.fcol h6{font-weight:400;font-size:15px;text-transform:uppercase;margin-bottom:12px}
.social{display:flex;gap:11px}
.social i{width:24px;height:24px;border-radius:3px;background:#6d9fcf}
.social i:last-child{background:#e9853c}
</style>
</head>
<body>
<div class="page">
  <div class="abs topbar"></div>

  <header>
    <div class="abs logo-mark"></div>
    <div class="abs logo-name">Nimbo 31</div>
    <div class="abs logo-tag">Enterprise Hosting</div>
    <nav class="abs topnav">
      <div><b>Dedicated Servers:</b>Corva Servers</div>
      <div><b>Virtual Servers</b>KelpVZ or Reef</div>
      <div><b>Cloud Servers</b>Stratovise Enterprise</div>
      <div><b>About Nimbo 31</b>Learn about us</div>
    </nav>
    <div class="abs buttons">
      <span style="width:113px">Nimbo 31</span>
      <span style="width:115px">Live Chat</span>
      <span style="width:108px">Email Us</span>
      <span style="width:115px">Get a Quote</span>
      <span style="width:114px">Client Login</span>
    </div>
  </header>

  <section class="abs hero">
    <div class="abs hero-art" role="img" aria-label="Illustration of figures carrying coloured puzzle pieces together"></div>
    <div class="abs hero-copy">
      <h2>Why we're different.</h2>
      <p>Fast response times !</p>
      <p>Your needs Matter !</p>
      <p>Enterprise Solutions ??</p>
    </div>
    <div class="abs dots"><i></i><i></i><i></i></div>
  </section>

  <section class="abs plan" style="left:24px">
    <h3><svg width="78" height="40" viewBox="0 0 78 40" fill="none" stroke="#555" stroke-width="2"><rect x="2" y="2" width="20" height="36"/><rect x="29" y="2" width="20" height="36"/><rect x="56" y="2" width="20" height="36"/><path d="M6 10h12M33 10h12M60 10h12M6 16h12M33 16h12M60 16h12"/></svg>Dedicated Servers</h3>
    <ul><li>Enterprise TowerBoard Servers</li><li>Fully Customized Configurations</li><li>Ready in hours</li><li>Corva Processors</li><li>IPMI Remote Management</li></ul>
    <div class="price">Starting at <strong>$599/mo</strong><a href="#">Learn More</a></div>
    <ul><li>Hardware Raid w/ Battery Backup</li><li>Up to 32GB Ram</li><li>Up to 16 Hot swap hard drives</li><li>SSD, SAS and SATA drive options</li><li>Any Operating System</li></ul>
  </section>

  <section class="abs plan" style="left:423px">
    <h3><svg width="54" height="40" viewBox="0 0 54 40" fill="none" stroke="#555" stroke-width="2"><path d="M12 36h30a10 10 0 0 0 0-20 14 14 0 0 0-27-3A11 11 0 0 0 12 36z"/></svg>Cloud Servers</h3>
    <ul><li>Stratovise Cloud</li><li>Fully redundant 100% uptime</li><li>Enterprise Ready</li></ul>
    <div class="price stacked">Starting at <strong>$99/mo</strong><a href="#">Learn More</a></div>
    <ul><li>Sub Point 1</li><li>Sub Point 2</li><li>Sub Point 3</li></ul>
  </section>

  <section class="abs plan" style="left:814px">
    <h3><svg width="26" height="40" viewBox="0 0 26 40" fill="none" stroke="#555" stroke-width="2"><rect x="3" y="2" width="20" height="36"/><path d="M7 10h12M7 16h12"/></svg>Virtual Servers</h3>
    <ul><li>KelpVZ or Reef</li><li>Ready in minutes</li><li>Affordable and reliable</li></ul>
    <div class="price stacked">Starting at <strong>$ 4. 95/mo</strong><a href="#">Learn More</a></div>
    <ul><li>Sub Point 1</li><li>Sub Point 2</li><li>Sub Point 3</li></ul>
  </section>

  <section class="abs hybrid">
    <div>Hybrid Solutions</div>
    <div>The best of both dedicated and cloud.</div>
    <div class="cost">5179/mo</div>
  </section>

  <section class="abs offers">
    <h4>Special Offers</h4>
    <div class="abs offer-photo" role="img" aria-label="Photo of hands typing on a laptop"></div>
    <p class="abs offer-text">Sed ut perspiciatis error sit voluptatem accusantium , totam rem aperiam, eaque ipsa quae ab illo</p>
    <div class="abs offer-link">Click Here &gt;&gt;</div>
  </section>

  <section class="abs difference">
    <h3>The Nimbo31 Difference</h3>
    <p class="intro">The service we offer is different and our approach is unique. We exceed every industry standard while remaining price competitive. Below are the top differentiators from the rest of the industry. Please see The Altura Difference for a comprehensive list.</p>
    <div class="abs tabs">
      <span class="on" style="width:112px">Network</span>
      <span style="width:90px">Facility</span>
      <span style="width:92px">Support</span>
      <span style="width:92px">Firewall</span>
      <span style="width:118px">VPN Access</span>
      <span style="width:90px">Servers</span>
      <span style="width:200px">Remote Server Control</span>
      <span style="width:76px;border-right:0">SLA</span>
    </div>
    <div class="abs tab-panel">
      <div class="abs feat" style="left:26px;top:42px"><h5>100% Uptime</h5><p>Our 2N Network delivers nonstop service 24-hours a day, every day of the year without downtime</p></div>
      <div class="abs feat" style="left:374px;top:42px"><h5>Multiple Premium Carriers</h5><p>Multiple carriers include Tierline, Corelink, nWave, Tidenet, Orbit Crossing, SkyHaul and more</p></div>
      <div class="abs feat" style="left:753px;top:38px"><h5>Carrier Grade Equipment</h5><p>Brand new direct from Brightfern Networks with 24/7 support and equipment replacement agreements</p></div>
      <div class="abs feat" style="left:30px;top:188px"><h5>Border Gateway Protocols (BGP)</h5><p>Our fully meshed network is resilient to fiber cuts, hardware failures and carrier outages</p></div>
      <div class="abs feat" style="left:374px;top:182px"><h5>High Availability Network</h5><p>Servers connect to two public switches for complete network redundancy and to eliminate downtime</p></div>
      <div class="abs feat" style="left:753px;top:178px"><h5>Scalable and Secure</h5><p>Your servers have a private network between them for gigabit communications</p></div>
    </div>
  </section>

  <section>
    <h3 class="abs section-title" style="left:51px;top:1880px">Customer Testimonial</h3>
    <div class="abs client a" style="left:53px">ByteReview</div>
    <div class="abs client b" style="left:406px">Berrywise</div>
    <div class="abs client c" style="left:750px">Chatterly</div>
    <div class="abs quote" style="left:53px"><b>Jo</b>"The experience was great, this was my first time using Pixelboard. Jo was professional throughout</div>
    <div class="abs quote" style="left:406px"><b>Jo</b>"The experience was great, this was my first time using Pixelboard. Jo was professional throughout</div>
    <div class="abs quote" style="left:750px"><b>Jo</b>"The experience was great, this was my first time using Pixelboard. Jo was professional throughout</div>
  </section>

  <section>
    <div class="abs feed-icon"></div>
    <h3 class="abs section-title feed-title">Chirper Feed</h3>
    <article class="abs tweet" style="left:86px"><time>Jun 30, 2012</time>Vexa Media Systems to Discuss Multiscreen Video Delivery Strategies at ProjectorCon 2012Vexa Media Systems to Discuss Multiscreen Video Delivery<a href="#">View More &gt;&gt;</a></article>
    <article class="abs tweet" style="left:441px"><time>Jun 30, 2012</time>Vexa Media Systems to Discuss Multiscreen Video Delivery Strategies at ProjectorCon 2012Vexa Media Systems to Discuss Multiscreen Video Delivery<a href="#">View More &gt;&gt;</a></article>
    <article class="abs tweet" style="left:796px"><time>Jun 30, 2012</time>Vexa Media Systems to Discuss Multiscreen Video Delivery Strategies at ProjectorCon 2012Vexa Media Systems to Discuss Multiscreen Video Delivery<a href="#">View More &gt;&gt;</a></article>
  </section>

  <footer class="abs footer">
    <div class="abs fcol" style="left:62px;top:36px"><h6>Main Navigation</h6>Dedicated Servers<br>Virtual Servers<br>Cloud Servers<br>About Nimbo 31</div>
    <div class="abs fcol" style="left:317px;top:52px">Additional Info<br>Terms of Service<br>Privacy Policy<br>Service Level Agreement</div>
    <div class="abs fcol" style="left:317px;top:173px">Referral Program<br>I Reseller Program</div>
    <div class="abs fcol" style="left:591px;top:52px">Support Center<br>Live Chat<br>Email Us</div>
    <div class="abs fcol" style="left:591px;top:153px">Get a Quote<br>Client Login</div>
    <div class="abs fcol" style="left:898px;top:48px"><h6>Social Media</h6></div>
    <div class="abs social" style="left:900px;top:100px"><i></i><i></i><i></i><i></i><i></i></div>
    <div class="abs fcol" style="left:900px;top:148px;font-size:13px">© 2012 nimbo31.com.au, All rights reserved</div>
  </footer>
</div>
</body>
</html>
```